Build a landing page to promote a service (dialler consultation and support).

We are a call centre consultation firm and we need a landing page to promote a service. The service is Tormalux dialler consultation and support.
If you do not know what Tormalux is, please do some quick "Zorvex" research for more information.
The landing page will be promoted with a paid advertisement, so we want something that is simple, and explains exactly what service we offer.
There are two objectives for the landing page:
1) A "call to action" which directs the user to a contact page, including a form plus all of our contact details.
2) A form for them viewers to enter their details to get a "FREE" quote for their project. This form should be placed on the main page.
Notes:
The call to action will require the viewer to enter their name, email, phone number as well as a description of their request. There will also need to be a drop down menu for the type of quote. This menu should have the following options:
1) Tormalux support
2) Tormalux hosting
3) Tormalux customisation
4) Other
We need 2 pages in total:
1) Main landing page
This is the home page. It will need to clearly indicate our services and our key selling features.
Services:
* Tormalux support
* Tormalux hosting
* Tormalux customisation
Key Selling Features:
* Australian based
* PCI complaint
* 10+ years of dialler and call centre experience
* we run a sister company which is a highly reputable 40 seat call centre, so we know first hand about call centre technology.
The main landing page will have an "about us" section with a few paragraphs about how we got started.
-------------------------------------------------------------------------
2) Contact page
All of our contact details will live on this page, as well as a contact form.
Other notes:
We will be self hosting the landing page.
We already have a domain name.
The design must be clean and incorporate our logo, as well as it's colours. (Logo attached)
We want a fully function HTML landing page, not just a "PSD" design.
The page must be mobile optimised.
Anyone using Tormalux software.

```html
<!DOCTYPE html>
<html lang="en">
<head>
<meta charset="utf-8">
<title>NimbleCall — Contact</title>
<link href="https://fonts.googleapis.com/css2?family=Montserrat:wght@400;500;600;700&display=swap" rel="stylesheet">
<style>
:root{
  --teal:#1fae8f;
  --blue:#1a73c5;
  --ink:#2b2b2b;
  --text:#4a4a4a;
  --muted:#9a9a9a;
  --panel:#efefef;
  --white:#ffffff;
  --line:#d6d6d6;
  --brand-grad:linear-gradient(90deg,var(--teal),var(--blue));
}
*{box-sizing:border-box;margin:0;padding:0}
html,body{width:1054px;height:1200px;overflow:hidden}
body{position:relative;font-family:'Montserrat',sans-serif;color:var(--text);background:var(--white)}
.abs{position:absolute}

/* header */
.site-header{left:0;top:0;width:1054px;height:107px;background:var(--white)}
.brand{left:141px;top:30px;display:flex;align-items:center;gap:8px}
.brand-dot{width:34px;height:34px;border-radius:50%;background:var(--blue)}
.brand-name{font-size:24px;font-weight:600;color:var(--teal)}
.header-phone{right:143px;top:17px;font-size:14px;font-weight:600;color:var(--blue);display:flex;align-items:center;gap:4px}
.main-nav{right:143px;top:58px;display:flex;align-items:center;gap:28px;font-size:13px;font-weight:600;color:#444}
.nav-cta{background:var(--teal);color:var(--white);padding:0 11px;height:30px;line-height:30px;margin-left:-8px}

/* hero */
.hero{left:0;top:107px;width:1054px;height:255px;background:linear-gradient(100deg,#5a4a40 0%,#8a7060 30%,#b99a7e 55%,#c9b79c 75%,#a9a59c 100%)}
.hero-title{left:0;top:107px;width:1054px;height:255px;display:flex;align-items:center;justify-content:center;font-size:58px;font-weight:700;color:var(--white);letter-spacing:1px}

/* contact section */
.contact-section{left:0;top:362px;width:1054px;height:604px;background:var(--panel)}
.section-title{left:0;top:396px;width:1054px;text-align:center;font-size:32px;font-weight:700;color:#555;letter-spacing:3px}
.section-intro{left:327px;top:451px;width:400px;text-align:center;font-size:12px;line-height:20px}
.address-title{left:141px;top:545px;font-size:23px;font-weight:700;color:var(--ink)}
.address-intro{left:141px;top:590px;width:330px;font-size:12px;line-height:20px}
.detail-icon{left:142px;width:44px;height:44px;border-radius:50%;background:var(--brand-grad);display:flex;align-items:center;justify-content:center;border:1px solid #14626c}
.detail-text{font-size:12px;font-weight:600;line-height:21px;color:#444}

/* form card */
.form-card{left:582px;top:530px;width:280px;height:362px;background:var(--white);box-shadow:0 0 6px rgba(0,0,0,.12)}
.form-title{left:582px;top:553px;width:280px;text-align:center;font-size:25px;font-weight:700;color:#4a4a4a}
.field{left:607px;width:240px;height:28px;border:1px solid var(--line);background:var(--white);display:flex;align-items:center;gap:6px;padding-left:4px;font-size:9.5px;color:#666}
.field-icon{width:18px;height:18px;border-radius:50%;background:#ececec;display:flex;align-items:center;justify-content:center}
.field-area{height:87px;align-items:flex-start;padding-top:4px}
.submit-btn{left:607px;top:826px;width:240px;height:28px;background:var(--brand-grad);color:var(--white);font-size:12px;font-weight:600;display:flex;align-items:center;justify-content:center}

/* footer */
.footer-rule{left:0;top:966px;width:1054px;height:3px;background:var(--brand-grad)}
.footer-brand{left:141px;top:1030px;display:flex;align-items:center;gap:10px}
.footer-dot{width:44px;height:44px;border-radius:50%;background:#c4c4c4}
.footer-name{font-size:28px;font-weight:600;color:#bdbdbd}
.footer-col h4{font-size:14px;font-weight:600;color:var(--blue);margin-bottom:14px}
.footer-col li{list-style:none;font-size:11px;line-height:22.4px;color:#333}
.social{left:789px;top:1039px;display:flex;gap:16px;align-items:center}
.social-dot{width:20px;height:20px;border-radius:50%;background:#111}
.footer-line{left:141px;top:1154px;width:770px;height:1px;background:#ddd}
.copyright{left:0;top:1166px;width:1054px;text-align:center;font-size:11px;font-weight:500;color:#555}
</style>
</head>
<body>

<header class="site-header abs"></header>
<div class="brand abs"><span class="brand-dot"></span><span class="brand-name">NimbleCall</span></div>
<div class="header-phone abs">
  <svg width="12" height="12" viewBox="0 0 24 24"><path fill="#1a73c5" d="M6.6 10.8a15 15 0 0 0 6.6 6.6l2.2-2.2c.3-.3.7-.4 1-.2 1.1.4 2.3.6 3.6.6.6 0 1 .4 1 1V20c0 .6-.4 1-1 1A17 17 0 0 1 3 4c0-.6.4-1 1-1h3.5c.6 0 1 .4 1 1 0 1.3.2 2.5.6 3.6.1.3 0 .7-.2 1z"/></svg>
  Phone: 555-204-7731
</div>
<nav class="main-nav abs">
  <span>Home</span><span>About Us</span><span>Services</span><span>News</span><span class="nav-cta">Contact Us</span>
</nav>

<div class="hero abs" role="img" aria-label="Photo of call centre agents wearing headsets"></div>
<h1 class="hero-title abs">NimbleCall</h1>

<section class="contact-section abs"></section>
<h2 class="section-title abs">Contact</h2>
<p class="section-intro abs">Lorem ipsum dolor sit amet, consectetur adipiscing elit, sed do eiusmor incididunt ut labore et dolore magna aliqua.</p>

<h3 class="address-title abs">NimbleCall Address</h3>
<p class="address-intro abs">Lorem ipsum dolor sit amet, consectetur adipiscing elit, sed doeiusmor incididunt ut labore et doloreorem eiusmor incididunt ut labore et dolore magna</p>

<div class="detail-icon abs" style="top:697px">
  <svg width="18" height="22" viewBox="0 0 18 22" fill="none" stroke="#fff" stroke-width="1.3"><path d="M9 21s7-7.5 7-12.5A7 7 0 0 0 2 8.5C2 13.5 9 21 9 21z"/><circle cx="9" cy="8.5" r="2.6"/></svg>
</div>
<div class="detail-text abs" style="left:199px;top:690px">Harbourline Plaza<br>4120 Kestrel Road, Suite 210<br>Marrowby, WA 98110</div>

<div class="detail-icon abs" style="top:767px">
  <svg width="22" height="22" viewBox="0 0 24 24" fill="none" stroke="#fff" stroke-width="1.3"><path d="M6.6 10.8a15 15 0 0 0 6.6 6.6l2.2-2.2c.3-.3.7-.4 1-.2 1.1.4 2.3.6 3.6.6.6 0 1 .4 1 1V20c0 .6-.4 1-1 1A17 17 0 0 1 3 4c0-.6.4-1 1-1h3.5c.6 0 1 .4 1 1 0 1.3.2 2.5.6 3.6.1.3 0 .7-.2 1z"/></svg>
</div>
<div class="detail-text abs" style="left:206px;top:773px">Phone:<br>555.318.6620</div>

<div class="detail-icon abs" style="top:829px">
  <svg width="22" height="16" viewBox="0 0 22 16" fill="none" stroke="#fff" stroke-width="1.3"><rect x="1" y="1" width="20" height="14"/><path d="M1 1l10 8 10-8M1 15l7-7M21 15l-7-7"/></svg>
</div>
<div class="detail-text abs" style="left:205px;top:826px">Email:<br>hello@nimblecall.example</div>

<div class="form-card abs"></div>
<h3 class="form-title abs">Contact Form</h3>
<div class="field abs" style="top:606px"><span class="field-icon"><svg width="10" height="10" viewBox="0 0 10 10" fill="none" stroke="#aaa"><circle cx="5" cy="3.5" r="2"/><path d="M1 9.5c0-2 2-3 4-3s4 1 4 3"/></svg></span>Name</div>
<div class="field abs" style="top:637px"><span class="field-icon"><svg width="10" height="8" viewBox="0 0 10 8" fill="none" stroke="#aaa"><rect x=".5" y=".5" width="9" height="7"/><path d="M.5 .5l4.5 4 4.5-4"/></svg></span>Email</div>
<div class="field abs" style="top:668px"><span class="field-icon"><svg width="10" height="10" viewBox="0 0 24 24" fill="none" stroke="#aaa" stroke-width="2"><path d="M6.6 10.8a15 15 0 0 0 6.6 6.6l2.2-2.2c.3-.3.7-.4 1-.2 1.1.4 2.3.6 3.6.6.6 0 1 .4 1 1V20c0 .6-.4 1-1 1A17 17 0 0 1 3 4c0-.6.4-1 1-1h3.5c.6 0 1 .4 1 1 0 1.3.2 2.5.6 3.6.1.3 0 .7-.2 1z"/></svg></span>Phone</div>
<div class="field abs" style="top:700px"><span class="field-icon"><svg width="10" height="10" viewBox="0 0 10 10" fill="none" stroke="#aaa"><rect x="1.5" y=".5" width="7" height="9"/><path d="M3 3h1M6 3h1M3 5.5h1M6 5.5h1"/></svg></span>Address</div>
<div class="field field-area abs" style="top:732px"><span class="field-icon"><svg width="10" height="10" viewBox="0 0 10 10" fill="none" stroke="#aaa"><rect x=".5" y="1.5" width="8" height="8"/><path d="M4 6l5-5"/></svg></span><span style="margin-top:3px">Comments</span></div>
<div class="submit-btn abs">Submit Here</div>

<div class="footer-rule abs"></div>
<div class="footer-brand abs"><span class="footer-dot"></span><span class="footer-name">NimbleCall</span></div>

<div class="footer-col abs" style="left:357px;top:1005px">
  <h4>Services</h4>
  <ul><li>Tormalux support</li><li>Tormalux hosting</li><li>Tormalux customisation</li><li>Other</li></ul>
</div>
<div class="footer-col abs" style="left:528px;top:1005px">
  <h4>Links</h4>
  <ul><li>Sed uerspatiem</li><li>Comnisteatusit</li><li>Sed ueratiem</li><li>Comnisteatusit</li></ul>
</div>
<div class="footer-col abs" style="left:663px;top:1005px">
  <h4>Company</h4>
  <ul><li>Sed uterspiciatis</li><li>Sed uerspiciatiem</li><li>Comnisteatusit</li><li>Perspiciatis unde</li></ul>
</div>
<div class="footer-col abs" style="left:789px;top:1005px"><h4>Connect</h4></div>
<div class="social abs">
  <svg width="22" height="16" viewBox="0 0 22 16"><rect x="0" y="0" width="22" height="16" fill="#111"/><path d="M0 0l11 9 11-9M0 16l8-8M22 16l-8-8" stroke="#fff" stroke-width="1.4" fill="none"/></svg>
  <span class="social-dot"></span><span class="social-dot"></span><span class="social-dot"></span>
</div>

<div class="footer-line abs"></div>
<p class="copyright abs">© 2018 All Rights are Reserved. Privacy Policy | Terms of Use | Contact</p>

</body>
</html>
```